Product Label & Logo for New Supplement

Your design will automatically be eliminated if you do NOT read this brief, because the description tells you about the brand you will be creating an identity for.Attached is the current label for the product. It is boring and doesn’t tell a story.We need you to unleash creative work to help patients with chronic pain diseases - like Multiple Sclerosis, Chronic Fatigue Syndrome, Lupus, and Fibromyalgia - no longer be defined by their disease. Velbrin Core is a new supplement developed by a neurologist to help patients with chronic pain feel better and have better days. It increases energy and stamina, saving the patient from having to take upwards of 40 different supplements.The label and logo need to convey that this supplement will give hurting patients new life.
Target Market(s)
People with fatigue, pain and inflammation
Industry/Entity Type
Supplement
Requirements
Must have
- Gender neutral, eye catching, all the ingredients listed in addition to logo design
Nice to have
- Custom logo, no generic fonts for name brand

```html
<!DOCTYPE html>
<html lang="en">
<head>
<meta charset="utf-8">
<title>Velbrin Core – Supplement Label</title>
<link href="https://fonts.googleapis.com/css2?family=Montserrat:wght@700;800&family=Roboto:wght@400;700&family=Roboto+Condensed:wght@400;700&display=swap" rel="stylesheet">
<style>
  :root {
    --navy: #1d3466;
    --navy-deep: #172a55;
    --teal: #2aa99b;
    --ink: #2a2f3a;
    --grey-tag: #e6e8eb;
    --grey-note: #eceef0;
    --page: #ffffff;
    --glow-a: #9fd8ff;
    --glow-b: #2f7fe0;
  }
  * { margin: 0; padding: 0; box-sizing: border-box; }
  html, body { width: 1032px; height: 1200px; overflow: hidden; background: var(--page); }
  body { font-family: "Roboto", Arial, sans-serif; color: var(--ink); position: relative; }

  .label { position: absolute; left: 0; top: 383px; width: 1032px; height: 427px; background: var(--page); }

  /* left panel */
  .directions, .caution { position: absolute; left: 25px; width: 292px; font-size: 12.5px; line-height: 16.5px; text-align: justify; }
  .directions { top: 17px; }
  .caution { top: 70px; }
  .lead { color: var(--teal); }
  .warning { position: absolute; left: 22px; width: 298px; top: 196px; text-align: center; font-family: "Roboto Condensed", sans-serif; font-weight: 700; font-size: 11px; line-height: 15px; color: #111; }
  .disclaimer { position: absolute; left: 30px; top: 256px; width: 287px; height: 42px; background: var(--grey-note); border-radius: 4px; padding: 3px 8px; font-size: 9.3px; line-height: 12px; }

  .band { position: absolute; left: 0; top: 305px; width: 695px; height: 122px; background: linear-gradient(90deg, var(--navy-deep), var(--navy)); color: #fff; }
  .distributor { position: absolute; left: 25px; top: 14px; font-size: 11.5px; line-height: 15px; color: #dfe6f3; }
  .distributor strong { color: #fff; }
  .website { position: absolute; left: 90px; top: 76px; font-size: 14px; color: #e5ebf5; }
  .format { position: absolute; left: 351px; top: 44px; font-size: 15px; letter-spacing: .5px; line-height: 25px; }
  .format strong { font-weight: 700; }

  /* centre panel */
  .brand-mark { position: absolute; left: 420px; top: 26px; width: 190px; display: flex; align-items: center; justify-content: center; gap: 7px; font-family: "Montserrat", sans-serif; font-weight: 800; font-size: 16px; color: var(--navy); }
  .brand-mark .dot { width: 11px; height: 11px; border-radius: 50%; background: var(--teal); }
  .product-name { position: absolute; left: 366px; width: 300px; top: 116px; text-align: center; font-family: "Montserrat", sans-serif; font-weight: 800; font-size: 30px; line-height: 40px; color: var(--teal); white-space: nowrap; }
  .tagline { position: absolute; left: 395px; top: 156px; width: 242px; height: 17px; background: var(--grey-tag); text-align: center; font-family: "Roboto Condensed", sans-serif; font-size: 10.5px; font-weight: 700; letter-spacing: 1.1px; line-height: 17px; color: #55595f; white-space: nowrap; }
  .benefits { position: absolute; left: 366px; width: 300px; top: 199px; list-style: none; text-align: center; font-size: 16.5px; line-height: 26.5px; color: var(--navy); white-space: nowrap; }
  .visual { position: absolute; left: 535px; top: 306px; width: 95px; height: 78px; border-radius: 50% 40% 45% 50%; background: radial-gradient(ellipse at 40% 55%, var(--glow-a), var(--glow-b) 55%, rgba(47,127,224,0) 75%); }

  /* facts panel */
  .facts { position: absolute; left: 725px; top: 14px; width: 284px; border: 1.5px solid var(--teal); border-radius: 6px; padding: 6px 10px 6px; font-family: "Roboto Condensed", sans-serif; font-size: 10px; line-height: 12.5px; color: #111; }
  .facts h2 { font-weight: 400; font-size: 22px; line-height: 26px; }
  .facts .rule { border-top: 1px solid #333; margin: 4px 0 3px; }
  .facts .row { display: grid; grid-template-columns: 1fr auto 46px; column-gap: 4px; white-space: nowrap; }
  .facts .row span:nth-child(n+2) { text-align: right; }
  .facts .row .wide { grid-column: 1 / 3; text-align: right; }
  .ingredients { position: absolute; left: 734px; top: 289px; width: 275px; font-family: "Roboto Condensed", sans-serif; font-size: 10px; line-height: 13px; }
  .marks { position: absolute; left: 739px; top: 376px; display: flex; gap: 18px; }
  .marks span { width: 26px; height: 26px; border-radius: 50%; background: #1a1a1a; }
</style>
</head>
<body>
<main class="label">
  <p class="directions"><span class="lead">DIRECTIONS :</span> Take two (2) tablets in the morning or take the first tablet at breakfast and the second at lunch.</p>
  <p class="caution"><span class="lead">CAUTION :</span> Do not exceed recommended dose. Pregnant or nursing mother, children under the age of 18, and individuals with a known medical condition should consult a physician before using this or any dietary supplement.</p>
  <p class="warning">KEEP OUT OF REACH OF CHILDREN. DO NOT USE IF SAFETY SEAL<br>IS DAMAGED OR MISSING. STORE IN A COOL, DRY PLACE.</p>
  <p class="disclaimer">*These statements have not been evaluated by the food and drug administration. This product is not intended to diagnose, treat, cure or prevent any disease.</p>

  <div class="brand-mark"><span class="dot"></span>Velbrin Core</div>
  <h1 class="product-name">VELBRIN CORE</h1>
  <p class="tagline">DON'T BE DEFINED BY YOUR ILLNESS</p>
  <ul class="benefits">
    <li>• INCREASES ENERGY</li>
    <li>• DECREASES INFLAMMATION</li>
    <li>• IMPROVES PERFORMANCE</li>
  </ul>

  <section class="band">
    <p class="distributor">DISTRIBUTED BY :<br><strong>Velbrin Core</strong><br>info@velbrin-labs.com</p>
    <p class="website">www.velbrin-labs.com</p>
    <p class="format">DIETARY SUPPLEMENT<br><strong>60</strong> TABLETS</p>
  </section>
  <div class="visual" role="img" aria-label="Glowing blue illustration of connected nerve cells"></div>

  <section class="facts">
    <h2>SUPPLEMENT FACTS</h2>
    <p>Serving Size : 2 Tablets<br>Serving per Container : 30</p>
    <div class="rule"></div>
    <div class="row"><span>Amount per Serving</span><span>%Daily</span><span>Value</span></div>
    <div class="rule"></div>
    <div class="row"><span>Vitamin C (Ascorbic Acid)</span><span>500 mg</span><span>556%</span></div>
    <div class="row"><span>Vitamin D3 (as Cholecalciferol)</span><span>5000 IU</span><span>625%</span></div>
    <div class="row"><span>Folate</span><span>1,666.67 mcg DFE</span><span>417%</span></div>
    <div class="row"><span class="wide">(1000 mcg Folic Acid)</span><span>151%</span></div>
    <div class="row"><span>Vitamin B12 (as Cyanocobalamin)</span><span>2000 mcg</span><span>83,333%</span></div>
    <div class="row"><span>Biotin</span><span>300 mcg</span><span>1000%</span></div>
    <div class="rule"></div>
    <div class="row"><span>Proprietary Blend</span><span>1130 mg</span><span>*</span></div>
    <p>N-Acetyl-L-Cysteine, Turmeric Root Extract, Green Coffee Bean Extract Folic acid</p>
    <div class="rule"></div>
    <p>*Daily Value not established.</p>
  </section>
  <p class="ingredients">Other Ingredients : Microcrystalline Cellulose, Stearic Acid, Dicalcium Phosphate, Croscarmellose Sodium, Magnesium Stearate, Silicon Dioxide, Pharmaceutical Glaze (Shellac, Povidone).</p>
  <div class="marks"><span></span><span></span></div>
</main>
</body>
</html>
```